Business Card Design

New business card design

Target Market(s)

Residential & Commercial Property Managers

Industry/Entity Type

Plumbing Services

Contact Information for Business Card

Name - Rowan Keddle, title - Director, Phone Number - 0431 286 517, email - rowan@tbk-plumbing.com.au, Company ABN - 73 215 904 386,

Font styles to use
Sans Serif

Colors
0054AA
0677BA
7BADD7
CADEEF
E8F1F8

```html
<!DOCTYPE html>
<html lang="en">
<head>
<meta charset="UTF-8">
<title>TBK Plumbing Services – Business Card</title>
<link href="https://fonts.googleapis.com/css2?family=Montserrat:wght@400;500;700&display=swap" rel="stylesheet">
<style>
  :root {
    --backdrop: #2d2e30;
    --card-top: #262d36;
    --card-bottom: #1c2129;
    --accent: #2fa6dc;
    --accent-deep: #0677ba;
    --ink-light: #ffffff;
    --ink-muted: #5c6876;
    --band-light: #ffffff;
  }
  * { margin: 0; padding: 0; box-sizing: border-box; }
  html, body {
    width: 1200px; height: 900px; overflow: hidden;
    background: var(--backdrop);
    font-family: "Montserrat", sans-serif;
  }
  .stage {
    position: relative; width: 1200px; height: 900px;
    display: flex; flex-direction: column; align-items: center; justify-content: center; gap: 44px;
  }
  .card {
    position: relative; width: 600px; height: 343px;
    border-radius: 18px; overflow: hidden;
    background: linear-gradient(160deg, var(--card-top), var(--card-bottom));
    border-bottom: 7px solid var(--accent);
    box-shadow: 0 14px 30px rgba(0,0,0,.45);
  }
  /* Front */
  .card-front { display: flex; align-items: center; justify-content: center; }
  .brand { display: flex; align-items: center; gap: 10px; white-space: nowrap; }
  .brand-dot { width: 16px; height: 16px; border-radius: 50%; background: var(--accent); flex: none; }
  .brand-name { font-weight: 500; letter-spacing: .08em; color: var(--ink-muted); }
  .card-front .brand-name { font-size: 30px; }
  /* Back */
  .card-back .brand { position: absolute; left: 28px; top: 142px; width: 222px; }
  .card-back .brand-name { color: var(--ink-light); font-size: 15px; letter-spacing: .02em; }
  .card-back .brand-dot { width: 11px; height: 11px; }
  .divider {
    position: absolute; left: 268px; top: 62px; width: 1px; height: 168px; background: var(--accent);
  }
  .contact { position: absolute; left: 290px; top: 60px; color: var(--ink-light); }
  .contact-name { font-size: 23px; font-weight: 700; color: var(--accent); line-height: 1.1; }
  .contact-title { font-size: 14px; margin: 4px 0 12px; }
  .contact-list { list-style: none; font-size: 13px; }
  .contact-list li { display: flex; align-items: center; gap: 9px; margin-bottom: 8px; }
  .contact-list svg { width: 13px; height: 13px; fill: var(--accent); flex: none; }
  .contact-abn { font-size: 13px; margin-top: 6px; }
  .contact-abn strong { font-weight: 700; }
  .band { position: absolute; }
  .band-accent { left: 0; width: 340px; bottom: 22px; height: 30px; background: var(--accent); }
  .band-light { left: 352px; right: 0; bottom: 52px; height: 26px; background: var(--band-light); }
</style>
</head>
<body>
<main class="stage">
  <section class="card card-front">
    <div class="brand">
      <span class="brand-dot"></span>
      <span class="brand-name">TBK Plumbing Services</span>
    </div>
  </section>

  <section class="card card-back">
    <div class="brand">
      <span class="brand-dot"></span>
      <span class="brand-name">TBK Plumbing Services</span>
    </div>
    <div class="divider"></div>
    <div class="contact">
      <p class="contact-name">Rowan Keddle</p>
      <p class="contact-title">Director</p>
      <ul class="contact-list">
        <li>
          <svg viewBox="0 0 24 24"><path d="M6.6 10.8a15.1 15.1 0 0 0 6.6 6.6l2.2-2.2a1 1 0 0 1 1-.25 11.4 11.4 0 0 0 3.6.57 1 1 0 0 1 1 1V20a1 1 0 0 1-1 1A17 17 0 0 1 3 4a1 1 0 0 1 1-1h3.5a1 1 0 0 1 1 1c0 1.25.2 2.45.57 3.57a1 1 0 0 1-.25 1z"/></svg>
          0431 286 517
        </li>
        <li>
          <svg viewBox="0 0 24 24"><path d="M2 5h20v2l-10 6L2 7zm0 4.3 10 6 10-6V19H2z"/></svg>
          rowan@tbk-plumbing.com.au
        </li>
        <li>
          <svg viewBox="0 0 24 24"><circle cx="12" cy="12" r="10"/></svg>
          www.tbk-plumbing.com.au
        </li>
      </ul>
      <p class="contact-abn"><strong>ABN</strong> - 73 215 904 386</p>
    </div>
    <div class="band band-accent"></div>
    <div class="band band-light"></div>
  </section>
</main>
</body>
</html>
```